Corvane Capital Business Cards

These are professional business cards that are for my family office.
Put fake emails and phone numbers as of now until I finalize those components. This family office controls my families investments, assets, and future. The cards should be professional.
..
.
.
.
I just uploaded another variation of a logo I would like to see as a business card to I am inbeteen which logo to use

Target Market(s)

business

Industry/Entity Type

business

Contact Information for Business Card

Professional, wealth related, finance related.

Requirements
Must have
• Logo

```html
<!DOCTYPE html>
<html lang="en">
<head>
<meta charset="utf-8">
<title>Corvane Capital Business Cards</title>
<link rel="stylesheet" href="https://fonts.googleapis.com/css2?family=Lato:wght@400;700&display=swap">
<style>
  :root {
    --stage: #2e2f31;
    --navy: #23273a;
    --navy-soft: #303549;
    --ink: #2f3140;
    --text: #2b2b2b;
    --grey: #a9a9ab;
    --paper: #ffffff;
  }
  * { box-sizing: border-box; margin: 0; padding: 0; }
  html, body {
    width: 1200px; height: 904px; overflow: hidden;
    background: var(--stage);
    font-family: "Lato", Arial, sans-serif;
  }
  .canvas { position: relative; width: 1200px; height: 904px; }

  .card {
    position: absolute; width: 560px; height: 320px;
    border-radius: 3px; overflow: hidden;
    box-shadow: 0 18px 40px rgba(0,0,0,.45);
  }

  /* back */
  .card-back { left: 120px; top: 110px; background: var(--navy); }
  .card-back .pattern-area {
    position: absolute; inset: 0;
    background: linear-gradient(100deg, var(--navy) 0%, var(--navy-soft) 50%, var(--navy) 100%);
  }
  .card-back .back-brand {
    position: absolute; left: 0; right: 0; top: 138px;
    display: flex; align-items: center; justify-content: center; gap: 10px;
    color: var(--paper); font-size: 15px; font-weight: 400;
    letter-spacing: 3px; text-transform: uppercase;
  }
  .back-brand .dot {
    width: 30px; height: 30px; border: 1.5px solid var(--paper); border-radius: 50%;
  }

  /* front */
  .card-front { left: 520px; top: 474px; background: var(--paper); color: var(--text); }
  .brand {
    position: absolute; right: 34px; top: 22px;
    display: flex; flex-direction: column; align-items: flex-end; gap: 12px;
  }
  .brand .mark-circle {
    width: 72px; height: 72px; border: 3px solid var(--ink); border-radius: 50%;
    margin-right: 60px;
  }
  .brand .brand-name {
    color: var(--ink); font-size: 20px; font-weight: 400;
    letter-spacing: 3px; text-transform: uppercase;
  }
  .rule-right {
    position: absolute; right: 24px; top: 134px; width: 240px; height: 1px; background: var(--text);
  }
  .address {
    position: absolute; right: 28px; top: 150px;
    text-align: right; font-size: 15px; line-height: 20px;
  }
  .person { position: absolute; left: 32px; top: 180px; }
  .person .name { font-size: 21px; font-weight: 700; color: #3a3a3a; }
  .person .role { font-size: 13px; margin-top: 2px; margin-left: 12px; }
  .rule-left {
    position: absolute; left: 30px; top: 228px; width: 270px; height: 1px; background: var(--text);
  }
  .contacts {
    position: absolute; left: 32px; top: 236px; list-style: none;
    font-size: 15px; line-height: 24px;
  }
  .contacts li { display: flex; align-items: center; gap: 12px; }
  .contacts svg { width: 16px; height: 16px; fill: var(--ink); }
  .bands { position: absolute; left: 0; top: 0; }
  .website {
    position: absolute; right: 22px; top: 268px;
    color: var(--paper); font-size: 14px; letter-spacing: .3px;
  }
</style>
</head>
<body>
<main class="canvas">

  <section class="card card-back">
    <div class="pattern-area" role="img" aria-label="Repeating embossed monogram pattern in dark navy gloss"></div>
    <div class="back-brand"><span class="dot"></span>Corvane Capital</div>
  </section>

  <section class="card card-front">
    <svg class="bands" width="560" height="320" viewBox="0 0 560 320" aria-hidden="true">
      <polygon points="345,262 560,262 560,292 330,292" fill="var(--ink)"/>
      <polygon points="40,300 318,300 330,292 560,292 560,306 40,306" fill="var(--grey)"/>
    </svg>

    <div class="brand">
      <span class="mark-circle"></span>
      <span class="brand-name">Corvane Capital</span>
    </div>
    <div class="rule-right"></div>

    <address class="address" style="font-style:normal">
      421, Address line goes here<br>45452, Country name
    </address>

    <div class="person">
      <p class="name">Elliot Marsh</p>
      <p class="role">Owner</p>
    </div>
    <div class="rule-left"></div>

    <ul class="contacts">
      <li>
        <svg viewBox="0 0 24 24"><path d="M6.6 10.8a15.1 15.1 0 0 0 6.6 6.6l2.2-2.2a1 1 0 0 1 1-.25 11.4 11.4 0 0 0 3.6.57 1 1 0 0 1 1 1V20a1 1 0 0 1-1 1A17 17 0 0 1 3 4a1 1 0 0 1 1-1h3.5a1 1 0 0 1 1 1c0 1.25.2 2.45.57 3.57a1 1 0 0 1-.25 1z"/></svg>
        044-987 654 321
      </li>
      <li>
        <svg viewBox="0 0 24 24"><path d="M2 5h20v14H2z M2 5l10 8 10-8" stroke="#fff" stroke-width="1.5"/></svg>
        info@corvanemail.com
      </li>
    </ul>

    <p class="website">www.corvanecapital.com</p>
  </section>

</main>
</body>
</html>
```